New Web Design Project

Number of Pages Required

1 page

Requirements
Must have
• An Overview / Background of the Business & Services(not for profit rescue animal farm)
• The Target Market / Audience you are trying to reach (animal lovers)
• Design Specifics; any preferences or ideas for Style, Colour, Imagery, etc (no preferences)

```html
<!DOCTYPE html>
<html lang="en">
<head>
<meta charset="utf-8">
<title>Cedar Hollow Farms</title>
<link href="https://fonts.googleapis.com/css2?family=Poppins:wght@400;500;600;700&family=Open+Sans:ital,wght@0,400;0,600;1,400&display=swap" rel="stylesheet">
<style>
:root{
  --green:#76c22b;
  --green-dark:#5fa31c;
  --ink:#1b1b1b;
  --text:#555;
  --white:#fff;
  --light:#f3f3f3;
  --dark:#232625;
  --forest:#3c5a2c;
  --grass:#6f8f3a;
  --heading:'Poppins',sans-serif;
  --body:'Open Sans',sans-serif;
}
*{margin:0;padding:0;box-sizing:border-box}
html,body{width:1200px;height:4327px;overflow:hidden;background:var(--white)}
body{position:relative;font-family:var(--body);color:var(--ink)}
.abs{position:absolute}
a{color:inherit;text-decoration:none}

/* hero */
.hero{left:0;top:0;width:1200px;height:770px;overflow:hidden}
.hero-photo{position:absolute;inset:0;background:linear-gradient(180deg,#2f3b23 0%,#4a5f30 35%,#6f8a3c 60%,#7e9b45 100%)}
.hero-photo::after{content:"";position:absolute;inset:0;background:rgba(0,0,0,.25)}
.brand{left:92px;top:48px;display:flex;align-items:center;gap:18px;color:var(--green);font-family:var(--heading);font-weight:600;font-size:24px}
.brand-dot{width:70px;height:70px;border-radius:50%;background:var(--green)}
.nav{left:552px;top:70px;display:flex;gap:30px;font-family:var(--heading);font-weight:600;font-size:16px;color:var(--white)}
.hero-title{left:0;width:1200px;top:278px;text-align:center;color:var(--white);font-family:var(--heading);font-weight:700;font-size:50px}
.hero-sub{left:0;width:1200px;top:362px;text-align:center;color:var(--white);font-size:20px;line-height:30px}
.hero-btn{left:485px;top:468px;width:202px;height:54px;border-radius:27px;background:#3a2a12;color:var(--white);font-family:var(--heading);font-size:20px;display:flex;align-items:center;justify-content:center}
.hero-curve{left:0;top:640px}

/* services */
.section-title{left:0;width:1200px;text-align:center;font-family:var(--heading);font-weight:700;font-size:40px;color:var(--ink)}
.section-title span{color:var(--green)}
.service{width:240px;text-align:center}
.service-ring{width:182px;height:182px;margin:0 auto;border:6px solid var(--green);border-radius:50%;display:flex;align-items:center;justify-content:center}
.service-art{width:110px;height:110px;border-radius:50%;background:linear-gradient(135deg,#e7e7e7,#cfcfcf)}
.service-name{margin-top:34px;font-family:var(--heading);font-weight:600;font-size:22px}

/* about */
.about{left:0;top:1304px;width:1200px;height:568px;overflow:hidden}
.about-photo{position:absolute;inset:0;background:linear-gradient(120deg,#c98a3f 0%,#8a4e22 45%,#4a3a1e 75%,#7b6a2e 100%)}
.about-green{position:absolute;left:0;top:0}
.about-title{left:100px;top:100px;color:var(--white);font-family:var(--heading);font-weight:700;font-size:36px}
.about-text{left:92px;top:198px;width:450px;color:var(--white);font-size:15px;line-height:24px}
.outline-btn{left:92px;top:412px;width:194px;height:56px;border:2px solid var(--white);border-radius:28px;color:var(--white);font-family:var(--heading);font-size:19px;display:flex;align-items:center;justify-content:center}

/* news */
.card{top:2089px;width:272px;height:480px;background:var(--white);box-shadow:0 4px 16px rgba(0,0,0,.18);border-radius:6px;overflow:hidden;text-align:center}
.card-photo{height:185px}
.date-pill{margin:32px auto 0;width:100px;height:30px;border:2px solid var(--green);border-radius:15px;font-size:13px;display:flex;align-items:center;justify-content:center}
.card-title{margin-top:22px;font-family:var(--heading);font-weight:700;font-size:21px;line-height:28px}
.card-text{margin:18px 20px 0;color:var(--text);font-size:14px;line-height:19px}
.card-link{margin-top:16px;color:var(--green);font-family:var(--heading);font-weight:600;font-size:14px}

/* testimonials */
.testimonials{left:0;top:2660px;width:1200px;height:478px;background:linear-gradient(90deg,#1f2321,#3a3e3a 50%,#242725)}
.testimonials::after{content:"";position:absolute;inset:0;background:rgba(0,0,0,.35)}
.t-title{left:0;width:1200px;top:60px;text-align:center;color:var(--white);font-family:var(--heading);font-weight:700;font-size:38px;z-index:1}
.avatar{left:208px;top:168px;width:184px;height:184px;border-radius:50%;border:7px solid var(--green);background:linear-gradient(135deg,#8c8c88,#5d5f5b);z-index:1}
.quote{left:447px;top:220px;width:590px;color:var(--white);font-style:italic;font-size:15px;line-height:24px;z-index:1}
.qmark{font-family:Georgia,serif;font-size:48px;font-weight:700;color:var(--white);z-index:1}
.t-name{left:447px;top:306px;color:var(--white);font-family:var(--heading);font-weight:700;font-size:24px;z-index:1}

/* contact */
.contact-bg{left:0;top:3139px;width:660px;height:720px;background:var(--light)}
.contact-photo{left:658px;top:3139px;width:542px;height:720px;background:linear-gradient(140deg,#9fb2ae,#c9b89a 45%,#7d8a4a 80%)}
.contact-title{left:92px;top:3186px;font-family:var(--heading);font-weight:700;font-size:40px}
.contact-title span{color:var(--green)}
.field{left:92px;width:494px;height:48px;background:var(--white);border:1px solid #ddd;font-size:13px;color:#999;padding:14px 12px}
.submit{left:92px;top:3687px;width:162px;height:46px;border-radius:23px;background:var(--green);color:var(--white);font-family:var(--heading);font-size:17px;display:flex;align-items:center;justify-content:center}

/* footer */
.footer{left:0;top:3790px;width:1200px;height:537px;overflow:hidden}
.footer-bg{position:absolute;inset:0;background:linear-gradient(180deg,#2b2e2c,#1c1e1d)}
.footer-bg::after{content:"";position:absolute;inset:0;background:rgba(0,0,0,.25)}
.footer-brand{left:420px;top:58px;display:flex;align-items:center;gap:26px;color:var(--white);font-family:var(--heading);font-weight:600;font-size:24px;z-index:1}
.footer-brand .brand-dot{width:110px;height:110px;background:var(--white)}
.col{z-index:1;color:var(--white)}
.col h3{font-family:var(--heading);font-weight:700;font-size:23px;margin-bottom:24px}
.col li{list-style:none;font-size:16px;line-height:33px}
.c-item{display:flex;align-items:center;gap:22px;font-size:16px;margin-bottom:26px}
.news-text{font-size:15px;line-height:22px;width:240px}
.news-input{margin-top:18px;width:228px;height:32px;background:var(--white);color:#777;font-size:12px;padding:8px 10px}
.send{margin-top:22px;width:116px;height:34px;border-radius:17px;background:var(--green);font-size:14px;display:flex;align-items:center;justify-content:center}
.copy{left:92px;top:486px;color:var(--white);font-size:14px;z-index:1}
.socials{left:955px;top:478px;display:flex;gap:12px;z-index:1}
.socials span{width:30px;height:30px;background:var(--white);border-radius:3px}
</style>
</head>
<body>

<header class="abs hero">
  <div class="hero-photo" role="img" aria-label="Goats grazing on a sunny meadow beneath tall forest trees"></div>
  <div class="abs brand"><span class="brand-dot"></span>Cedar Hollow Farms.</div>
  <nav class="abs nav"><a>Home</a><a>Services</a><a>About Us</a><a>Blog</a><a>Testimonials</a><a>Contact Us</a></nav>
  <h1 class="abs hero-title">Welcome to Cedar Hollow Farms</h1>
  <p class="abs hero-sub">Lorem ipsum dolor sit amet, consectetur adipiscing elit<br>Etiam at quam metus.</p>
  <a class="abs hero-btn">View More</a>
  <svg class="abs hero-curve" width="1200" height="130" viewBox="0 0 1200 130">
    <path d="M0 30 Q560 170 1200 40 L1200 130 L0 130 Z" fill="#fff"/>
    <path d="M0 30 Q560 170 1200 40" fill="none" stroke="#76c22b" stroke-width="6"/>
  </svg>
</header>

<h2 class="abs section-title" style="top:820px">Our <span>Services</span></h2>
<div class="abs service" style="left:215px;top:960px"><div class="service-ring"><div class="service-art" role="img" aria-label="Icon of a cat with a medical cross"></div></div><div class="service-name">Rescue Animal</div></div>
<div class="abs service" style="left:480px;top:960px"><div class="service-ring"><div class="service-art" role="img" aria-label="Icon of a hand holding a heart with a paw"></div></div><div class="service-name">Caring Animal</div></div>
<div class="abs service" style="left:746px;top:960px"><div class="service-ring"><div class="service-art" role="img" aria-label="Icon of a cow with a heart"></div></div><div class="service-name">Animal Sanctuary</div></div>

<section class="abs about">
  <div class="about-photo" role="img" aria-label="Two cows standing in a field at golden sunset"></div>
  <svg class="about-green" width="620" height="568" viewBox="0 0 620 568">
    <path d="M0 0 L460 0 Q640 284 380 568 L0 568 Z" fill="#76c22b"/>
  </svg>
  <h2 class="abs about-title">About us</h2>
  <p class="abs about-text">Lorem ipsum dolor sit amet, consectetur adipiscing elit. Etiam at quam metus. In eget dolor magna. Interdum et malesuada fames ac ante ipsum primis in faucibus. Sed vitae ultrices magna, et dictum lacus. Nam sit amet tristique lorem, ut elementum sem. Vestibulum quis tellus sit amet diam vestibulum imperdiet.</p>
  <a class="abs outline-btn">Read More</a>
</section>

<h2 class="abs section-title" style="top:1975px"><span>Our Latest</span> News</h2>
<article class="abs card" style="left:164px"><div class="card-photo" role="img" aria-label="Donkey looking over a wooden fence" style="background:linear-gradient(135deg,#a29a8a,#6c6253)"></div><div class="date-pill">Jan 8,2019</div><h3 class="card-title">Standard Lorem<br>Ipsum passage</h3><p class="card-text">Lorem ipsum dolor sit amet, consectetur adipiscing elit, sed do eiusmod tempor incididunt.</p><div class="card-link">Read More &gt;&gt;</div></article>
<article class="abs card" style="left:473px"><div class="card-photo" role="img" aria-label="Hand stroking a white horse" style="background:linear-gradient(135deg,#d8dad6,#8f968c)"></div><div class="date-pill">Jan 8,2019</div><h3 class="card-title">Standard Lorem<br>Ipsum passage</h3><p class="card-text">Lorem ipsum dolor sit amet, consectetur adipiscing elit, sed do eiusmod tempor incididunt.</p><div class="card-link">Read More &gt;&gt;</div></article>
<article class="abs card" style="left:770px"><div class="card-photo" role="img" aria-label="Farmer checking cows in a barn" style="background:linear-gradient(135deg,#6e6a5e,#3d4a4f)"></div><div class="date-pill">Jan 8,2019</div><h3 class="card-title">Standard Lorem<br>Ipsum passage</h3><p class="card-text">Lorem ipsum dolor sit amet, consectetur adipiscing elit, sed do eiusmod tempor incididunt.</p><div class="card-link">Read More &gt;&gt;</div></article>

<section class="abs testimonials" role="img" aria-label="Dairy cows in a dim barn behind the testimonial">
  <h2 class="abs t-title">Testimonals</h2>
  <div class="abs avatar" role="img" aria-label="Portrait of the reviewer"></div>
  <span class="abs qmark" style="left:414px;top:170px">&ldquo;</span>
  <p class="abs quote">Lorem ipsum dolor sit amet, consectetur adipiscing elit. Etiam at quam metus. In eget dolor magna. Interdum et malesuada fames ac ante ipsum primis in faucibus. Sed vitae ultrices magna, et dictum lacus.</p>
  <span class="abs qmark" style="left:746px;top:256px">&rdquo;</span>
  <div class="abs t-name">-Daniel</div>
</section>

<div class="abs contact-bg"></div>
<div class="abs contact-photo" role="img" aria-label="Father and child feeding hay to a horse"></div>
<h2 class="abs contact-title"><span>Contact</span> Us</h2>
<div class="abs field" style="top:3292px">Name</div>
<div class="abs field" style="top:3364px">Email</div>
<div class="abs field" style="top:3433px">Address</div>
<div class="abs field" style="top:3505px;height:139px">Message</div>
<a class="abs submit">Submit</a>

<footer class="abs footer">
  <div class="footer-bg" role="img" aria-label="Cows in a barn with a farmer, darkened"></div>
  <svg class="abs" style="left:0;top:0;z-index:1" width="1200" height="60" viewBox="0 0 1200 60">
    <path d="M0 0 L1200 0 L1200 12 Q600 -10 0 50 Z" fill="#f3f3f3"/>
  </svg>
  <div class="abs footer-brand"><span class="brand-dot"></span>Cedar Hollow Farms.</div>
  <div class="abs col" style="left:124px;top:196px"><h3>Information</h3><ul><li>Home</li><li>Services</li><li>About Us</li><li>Blog</li><li>Testimonials</li><li>Contact Us</li></ul></div>
  <div class="abs col" style="left:456px;top:196px"><h3>Contact Us</h3>
    <div class="c-item"><svg width="18" height="24" viewBox="0 0 18 24"><path d="M9 0C4 0 0 4 0 9c0 6 9 15 9 15s9-9 9-15c0-5-4-9-9-9zm0 12a3 3 0 110-6 3 3 0 010 6z" fill="#fff"/></svg><span>48 Meadowlark Lane<br><span style="display:block;margin-top:14px">FL 30418</span></span></div>
    <div class="c-item"><svg width="20" height="20" viewBox="0 0 24 24"><path d="M6.6 10.8a15 15 0 006.6 6.6l2.2-2.2c.3-.3.7-.4 1-.2 1.1.4 2.3.6 3.6.6.6 0 1 .4 1 1V20c0 .6-.4 1-1 1A17 17 0 013 4c0-.6.4-1 1-1h3.5c.6 0 1 .4 1 1 0 1.3.2 2.5.6 3.6.1.3 0 .7-.2 1z" fill="#fff"/></svg>+0800 555 0142</div>
    <div class="c-item"><svg width="20" height="16" viewBox="0 0 20 16"><rect x="1" y="1" width="18" height="14" fill="none" stroke="#fff" stroke-width="1.6"/><path d="M1 1l9 8 9-8" fill="none" stroke="#fff" stroke-width="1.6"/></svg>hello@cedarhollowfarms.org</div>
  </div>
  <div class="abs col" style="left:877px;top:196px"><h3>Newsletter</h3>
    <p class="news-text">It is a long established fact that a reader will be distracted</p>
    <div class="news-input">Enter the Email</div>
    <div class="send">Send</div>
  </div>
  <div class="abs copy">© 2019 Cedar Hollow Farms. All Rights Reserved.</div>
  <div class="abs socials"><span></span><span></span><span></span><span></span></div>
</footer>

</body>
</html>
```